New Business Card Design Project

We require a business card design for Vexalund, a newly established Indian company.
Our focus is on the development, manufacturing, and export of a diverse array of pharmaceutical products on a global scale. The card should convey a professional appearance, as our primary markets are in Africa, China, and Southeast Asian nations.
We envision a two-sided business card, with the reverse side dedicated to a logo set against a solid color or an elegantly designed pattern. The corners should be rounded. We would appreciate seeing both horizontal and vertical design options. We trust the designer to utilize their expertise in creating this design.

The content for the business card is included in the attached Word file.

Target Market(s)

Our primary markets are in Africa, China, and Southeast Asian, Latin America, Maldives, Sri Lanka

Industry/Entity Type

Pharmaceutical Manufacturing and Export

Contact Information for Business Card

Colors

Designer to choose colors to be used in the design.

Requirements
Must have
• The reverse side of the business card features solely the logo along with the tagline, "Healing for All."
Should not have
• The logo should not exceed two instances, encompassing both the front and back sides of the card.

```html
<!DOCTYPE html>
<html lang="en">
<head>
<meta charset="utf-8">
<title>Vexalund Business Card</title>
<link rel="stylesheet" href="https://fonts.googleapis.com/css2?family=Lato:ital,wght@0,300;0,400;0,700;1,400&family=Libre+Baskerville:ital@1&display=swap">
<style>
  :root {
    --backdrop: #1f2023;
    --brand-blue: #2ba7e0;
    --brand-coral: #f0654f;
    --paper: #ffffff;
    --ink: #4a4a4a;
    --ink-soft: #6b6b6b;
  }
  * { margin: 0; padding: 0; box-sizing: border-box; }
  html, body {
    width: 1200px; height: 952px; overflow: hidden;
    background: var(--backdrop);
    font-family: "Lato", sans-serif;
  }
  .canvas {
    position: relative; width: 1200px; height: 952px;
  }
  .card {
    position: absolute; left: 250px; width: 700px; height: 400px;
    border-radius: 18px; overflow: hidden;
  }
  .card--front { top: 60px; background: var(--paper); }
  .card--back { top: 492px; background: var(--brand-blue); }

  /* front */
  .name-tab {
    position: absolute; left: 0; top: 34px; width: 30px; height: 44px;
    background: var(--brand-blue);
  }
  .holder {
    position: absolute; left: 52px; top: 30px;
  }
  .holder__name {
    font-size: 30px; font-weight: 400; letter-spacing: 0.5px; line-height: 1.1;
    color: var(--brand-blue);
  }
  .holder__name .surname { color: var(--brand-coral); font-weight: 700; }
  .holder__role {
    font-size: 19px; font-weight: 300; color: var(--ink); margin-top: 2px;
  }
  .contacts {
    position: absolute; left: 52px; top: 150px; list-style: none;
  }
  .contacts li {
    display: flex; align-items: flex-start; gap: 10px;
    font-size: 14px; color: var(--ink-soft); line-height: 1.3;
    margin-bottom: 10px;
  }
  .contacts svg { flex: none; width: 18px; height: 18px; margin-top: 1px; }
  .accent-rule {
    position: absolute; left: 0; top: 318px; width: 700px; height: 2px;
    background: var(--brand-coral);
  }
  .brand-lockup {
    position: absolute; right: 44px; top: 150px;
    display: flex; align-items: center; gap: 16px;
    background: var(--paper); padding: 10px 12px;
  }
  .brand-lockup__dot {
    width: 44px; height: 44px; border-radius: 50%; background: var(--brand-coral);
  }
  .brand-lockup__name {
    font-size: 44px; font-weight: 700; color: var(--brand-blue);
  }

  /* back */
  .back-lockup {
    position: absolute; inset: 0;
    display: flex; flex-direction: column; align-items: center; justify-content: center;
    color: var(--paper);
  }
  .back-lockup__name {
    font-size: 66px; font-weight: 700; letter-spacing: 1px; line-height: 1;
  }
  .tagline {
    display: flex; align-items: center; gap: 10px; margin-top: 10px;
    font-family: "Libre Baskerville", serif; font-style: italic; font-size: 20px;
  }
  .tagline::before, .tagline::after {
    content: ""; width: 40px; height: 1.5px; background: var(--paper);
  }
</style>
</head>
<body>
<main class="canvas">
  <section class="card card--front" aria-label="Business card front">
    <div class="name-tab"></div>
    <div class="holder">
      <h1 class="holder__name">ARJUN K. <span class="surname">MALVADE</span></h1>
      <p class="holder__role">CEO/Vexalund</p>
    </div>
    <ul class="contacts">
      <li>
        <svg viewBox="0 0 18 18" aria-hidden="true"><rect width="18" height="18" rx="4" fill="#f0654f"/><path d="M9 3.5a3.5 3.5 0 0 0-3.5 3.5c0 2.6 3.5 7 3.5 7s3.5-4.4 3.5-7A3.5 3.5 0 0 0 9 3.5z" fill="#fff"/><circle cx="9" cy="7" r="1.3" fill="#f0654f"/></svg>
        <span>12, Sunrise Colony, Nashik,<br>422001, India</span>
      </li>
      <li>
        <svg viewBox="0 0 18 18" aria-hidden="true"><rect width="18" height="18" rx="4" fill="#2ba7e0"/><path d="M6 4l2 2.4-1.1 1.3a6 6 0 0 0 3.4 3.4l1.3-1.1L14 12l-1.3 1.6C8.5 13.4 4.6 9.5 4.4 5.3z" fill="#fff"/></svg>
        <span>+919800012345</span>
      </li>
      <li>
        <svg viewBox="0 0 18 18" aria-hidden="true"><rect width="18" height="18" rx="4" fill="#2ba7e0"/><rect x="4" y="5.5" width="10" height="7" fill="none" stroke="#fff" stroke-width="1.3"/><path d="M4 5.5l5 4 5-4" fill="none" stroke="#fff" stroke-width="1.3"/></svg>
        <span>amalvade@vexalund.com</span>
      </li>
      <li>
        <svg viewBox="0 0 18 18" aria-hidden="true"><rect width="18" height="18" rx="4" fill="#2ba7e0"/><path d="M9 4l4 10-4-2.5L5 14z" fill="#fff"/></svg>
        <span>amalvade@vexalund.com</span>
      </li>
    </ul>
    <div class="accent-rule"></div>
    <div class="brand-lockup">
      <span class="brand-lockup__dot"></span>
      <span class="brand-lockup__name">Vexalund</span>
    </div>
  </section>

  <section class="card card--back" aria-label="Business card back">
    <div class="back-lockup">
      <p class="back-lockup__name">Vexalund</p>
      <p class="tagline">Healing for All</p>
    </div>
  </section>
</main>
</body>
</html>
```